Mens Jewellery Homepage - Modern, Stylish Mens Ring Brand - Homepage

Project Overview: KestrelHoops.com is a men's accessories brand specializing in high-quality mens rings.

The objective of this redesign is to create a modern, visually appealing homepage that is easy to navigate, showcases a wide range of rings, highlights personalization options, and builds trust with customers.

The new design should make a strong impression while reflecting the brand's premium quality and commitment to craftsmanship.

The focus will be on a sleek aesthetic that aligns with the tastes of men shopping for wedding bands, engagement rings, or fashion accessories.

Objectives:

Modern and Sleek Aesthetic:

A clean, minimalist design that emphasizes high-quality product imagery and thoughtful use of space.
Contemporary color palette that conveys elegance and sophistication, with accents that highlight key elements without overwhelming the user.

Consistent and easy-to-read typography that reflects the brand’s modern and masculine identity.

Showcasing Products:
Hero Section: A image to show off 3 or 4 ring designs that could be used for weddings or fashion.

Product Highlights: Below the hero banner, showcase product categories by color (see current website for colors)

Featured Products: Display a selection of “Top Rated” or “Customer Favorites” rings to help guide users toward popular choices.

Personalization Section:
A dedicated section promoting the ability to personalize rings, emphasizing features like engraving with names, dates, or special messages.
Include lifestyle images of personalized rings to inspire customers and give them an idea of what’s possible.
Use callouts such as “Make It Yours” or “Personalize Your Ring” to encourage users to explore the customization options available for each product.

Building Trust:

A space to show 5 or 6 testimonials and other trust elements

Symbols / text to show

free delivery
free returns
every ring stock
fast delivery
customer images (from reviews)

Driving Conversions:
Include a prominent call-to-action (CTA) button in the hero section with text like “Shop Now” or “Discover Our Collections.”

User Experience:
Fast, easy-to-navigate layout with simple and intuitive categories. Product categories and main sections should be clearly visible and easy to access without overwhelming the user.
Design the homepage to feel cohesive and uncluttered, with a logical flow from product discovery to personalization and checkout.

Visual Elements and Imagery:
Use ring images from our site, but add backgrounds etc to make the image on the homepage more interesting.

Personalization Options: Use visual representations (like ring mockups) showing where personalization options (such as engravings) would appear on the product.

I like (and would like to see some different designs from our current design)
Vorm.com for design
ridgeloops.com

Target Market(s)

Men - 20 to 35

Number of Pages Required

1 page

Requirements
Must have
• Easy navigation, Trust, Modern, Clean,
Nice to have
• Would like to see Different designs like Vorm.com - RidgeLoops.com

```html
<!DOCTYPE html>
<html lang="en">
<head>
<meta charset="utf-8">
<title>Kestrel Hoops – Men's Rings</title>
<link href="https://fonts.googleapis.com/css2?family=Montserrat:ital,wght@0,400;0,500;0,600;1,400&display=swap" rel="stylesheet">
<style>
:root{
  --ink:#1f1f1f;
  --dark:#262626;
  --light:#f2f2f2;
  --white:#ffffff;
  --yellow:#ffc400;
  --yellow-soft:#ffeaa6;
  --star:#f5a300;
  --hero-blue:#2f6ea3;
  --hero-orange:#c4600f;
  --cat-black:#000000;
  --cat-silver:#54575b;
  --cat-blue:#0b3270;
  --cat-gold:#e2aa2a;
  --cat-brown:#83553f;
  --cat-rose:#d9985f;
}
*{box-sizing:border-box;margin:0;padding:0}
html,body{width:1200px;height:4474px;overflow:hidden}
body{font-family:"Montserrat",sans-serif;color:var(--ink);background:var(--light);position:relative}
a{color:inherit;text-decoration:none}

/* header */
.topbar{position:absolute;left:0;top:0;width:1200px;height:90px;background:var(--dark)}
.brand{position:absolute;display:flex;align-items:center;gap:12px}
.brand-dot{width:58px;height:58px;border:3px solid currentColor;border-radius:50%}
.brand-name{font-weight:600;font-size:19px;letter-spacing:2px}
.topbar .brand{left:108px;top:16px;color:var(--white)}
.search{position:absolute;left:575px;top:30px;width:417px;height:34px;border:1px solid #9a9a9a;border-radius:4px;background:var(--dark);display:flex;overflow:hidden}
.search span{flex:1;color:#cfcfcf;font-size:15px;padding:7px 16px}
.search i{width:58px;background:var(--yellow);display:flex;align-items:center;justify-content:center}
.top-icons{position:absolute;left:1022px;top:30px;display:flex;gap:14px}

.navbar{position:absolute;left:0;top:90px;width:1200px;height:49px;background:var(--yellow-soft);display:flex;justify-content:center;gap:46px;align-items:center;font-size:14px;font-weight:500;padding-left:30px}
.navbar a{display:flex;align-items:center;gap:6px}

/* hero */
.hero{position:absolute;top:139px;left:0;width:1200px;height:538px}
.hero-tile{position:absolute;overflow:hidden}
.tile-blue{left:0;top:0;width:601px;height:257px;background:var(--hero-blue)}
.tile-orange{left:0;top:257px;width:601px;height:281px;background:var(--hero-orange)}
.tile-grey{left:601px;top:0;width:599px;height:538px}
.hero-photo{position:absolute;inset:0;background:radial-gradient(circle at 60% 35%,#d8d8d8 0,#a9a9a9 35%,#8a8a8a 75%)}
.ring-art{position:absolute;border-radius:50%}
.hero-title{position:absolute;color:var(--white);font-weight:600;line-height:1.25;z-index:1}
.btn{display:inline-block;background:var(--yellow);color:var(--ink);font-size:15px;font-weight:500;border-radius:4px;text-align:center}
.hero .btn{position:absolute;width:136px;height:33px;line-height:33px;z-index:1}

/* section headings */
.sec-title{position:absolute;left:0;width:1200px;display:flex;justify-content:center}
.sec-title h2{font-weight:500;font-size:35px;padding:0 26px;border-left:3px solid var(--yellow);border-right:3px solid var(--yellow);line-height:56px}
.on-dark h2{color:var(--white)}

/* categories */
.categories{position:absolute;top:677px;left:0;width:1200px;height:805px;background:var(--light)}
.cat-grid{position:absolute;left:111px;top:197px;display:grid;grid-template-columns:repeat(3,299px);column-gap:40px;row-gap:47px}
.cat-card{height:236px;border-radius:14px;position:relative;box-shadow:0 6px 12px rgba(0,0,0,.18);color:var(--white);overflow:hidden}
.cat-card .ring-art{left:105px;top:26px;width:90px;height:130px}
.cat-card span{position:absolute;left:0;right:0;bottom:30px;text-align:center;font-size:20px;font-weight:500}

/* products */
.products{position:absolute;top:1482px;left:0;width:1200px;height:1117px;background:var(--dark)}
.tabs{position:absolute;left:426px;top:205px;display:flex;height:47px;border:1px solid #9a9a9a}
.tabs a{width:174px;display:flex;align-items:center;justify-content:center;font-size:14px;color:var(--white)}
.tabs .active{background:var(--yellow);color:var(--ink)}
.prod-grid{position:absolute;left:111px;top:297px;display:grid;grid-template-columns:repeat(4,228px);column-gap:22px;row-gap:50px}
.prod-card{height:299px;border:1.5px solid #cfcfcf;border-radius:8px;position:relative;color:var(--white)}
.stars{color:var(--star);font-size:13px;letter-spacing:1px}
.prod-card .stars{position:absolute;right:16px;top:12px}
.prod-card .ring-art{left:60px;top:44px;width:108px;height:110px}
.prod-card p{position:absolute;left:12px;right:12px;top:186px;text-align:center;font-size:11.5px;line-height:20px;color:#e6e6e6}
.prod-card strong{position:absolute;left:0;right:0;top:256px;text-align:center;font-size:20px;font-weight:600;color:var(--yellow)}
.products .view-more{position:absolute;left:532px;top:997px;width:137px;height:35px;line-height:35px;font-size:15px}

/* engraving */
.engrave{position:absolute;top:2599px;left:0;width:1200px;height:600px}
.engrave h2{position:absolute;left:111px;top:110px;padding-left:31px;border-left:3px solid var(--yellow);font-size:35px;font-weight:500;line-height:47px;width:540px}
.engrave p{position:absolute;left:111px;top:288px;width:460px;font-size:15.5px;line-height:26px;color:#333}
.engrave .btn{position:absolute;left:111px;top:404px;width:138px;height:35px;line-height:35px}
.engrave-back{position:absolute;left:691px;top:123px;width:398px;height:346px;background:var(--yellow);border-radius:14px}
.engrave-photo{position:absolute;left:657px;top:87px;width:397px;height:347px;border-radius:12px;box-shadow:0 8px 18px rgba(0,0,0,.25);background:radial-gradient(circle at 50% 55%,#c97a3a 0,#9c5a2c 22%,#d8cfc6 45%,#ece8e3 80%)}

/* testimonials */
.testimonials{position:absolute;top:3155px;left:0;width:1200px;height:588px}
.testi-grid{position:absolute;left:111px;top:107px;display:grid;grid-template-columns:repeat(3,306px);column-gap:31px;row-gap:35px}
.testi-card{height:180px;background:var(--white);border-radius:10px;box-shadow:0 4px 12px rgba(0,0,0,.15);position:relative}
.testi-card p{position:absolute;left:18px;right:12px;top:18px;font-size:10.5px;font-style:italic;line-height:22px;color:#666}
.avatar{position:absolute;left:18px;top:100px;width:62px;height:62px;border-radius:50%;background:linear-gradient(135deg,#c9b8a6,#6f5d4d)}
.testi-card .who{position:absolute;left:98px;top:108px;font-size:16px;font-weight:500}
.testi-card .stars{position:absolute;left:98px;top:131px;font-size:15px}

/* benefits */
.benefits{position:absolute;top:3743px;left:0;width:1200px;height:412px;background:var(--dark)}
.benefit{position:absolute;top:190px;width:240px;text-align:center;color:var(--white);font-size:20px;font-weight:500}
.benefit svg{display:block;margin:0 auto 22px}

/* footer */
.footer{position:absolute;top:4155px;left:0;width:1200px;height:319px;background:var(--light)}
.footer .brand{left:111px;top:31px;color:var(--ink)}
.footer .about{position:absolute;left:111px;top:118px;width:390px;font-size:15px;line-height:23px;color:#444}
.foot-col{position:absolute;top:52px}
.foot-col h3{font-size:20px;font-weight:500;margin-bottom:14px}
.foot-col li{list-style:none;font-size:15px;line-height:25px;color:#555}
.foot-rule{position:absolute;left:111px;top:253px;width:978px;height:1px;background:#999}
.copyright{position:absolute;left:111px;top:276px;font-size:15px;color:#333}
.pay{position:absolute;left:771px;top:275px;display:flex;gap:8px}
.pay i{width:36px;height:20px;border-radius:3px;background:#c9c9c9}
</style>
</head>
<body>

<header class="topbar">
  <a class="brand" href="#"><span class="brand-dot"></span><span class="brand-name">KESTREL HOOPS</span></a>
  <div class="search"><span>Search</span><i><svg width="16" height="16" viewBox="0 0 16 16"><circle cx="6.5" cy="6.5" r="4.5" fill="none" stroke="#1f1f1f" stroke-width="2"/><path d="M10 10l4 4" stroke="#1f1f1f" stroke-width="2"/></svg></i></div>
  <div class="top-icons">
    <svg width="22" height="24" viewBox="0 0 22 24"><circle cx="11" cy="7" r="5" fill="none" stroke="#fff" stroke-width="1.8"/><path d="M2 23c0-6 4-9 9-9s9 3 9 9" fill="none" stroke="#fff" stroke-width="1.8"/></svg>
    <svg width="26" height="24" viewBox="0 0 26 24"><path d="M1 2h4l3 14h14l3-10H7" fill="none" stroke="#fff" stroke-width="1.8"/><circle cx="10" cy="21" r="2" fill="#fff"/><circle cx="20" cy="21" r="2" fill="#fff"/></svg>
  </div>
</header>

<nav class="navbar">
  <a href="#">Shop By Material <svg width="10" height="6" viewBox="0 0 10 6"><path d="M1 1l4 4 4-4" fill="none" stroke="#1f1f1f" stroke-width="1.5"/></svg></a>
  <a href="#">Shop By Color <svg width="10" height="6" viewBox="0 0 10 6"><path d="M1 1l4 4 4-4" fill="none" stroke="#1f1f1f" stroke-width="1.5"/></svg></a>
  <a href="#">Try At Home</a>
</nav>

<section class="hero">
  <div class="hero-tile tile-blue">
    <div class="ring-art" role="img" aria-label="Two vintage wood and meteorite men's rings" style="left:330px;top:95px;width:252px;height:139px;background:radial-gradient(ellipse,#6b4a36 0,#3e5d78 55%,rgba(47,110,163,0) 72%)"></div>
    <h1 class="hero-title" style="left:111px;top:50px;font-size:34px">Romantic<br>Vintage Sublime</h1>
    <a class="btn" href="#" style="left:111px;top:160px">Shop Now</a>
  </div>
  <div class="hero-tile tile-orange">
    <div class="ring-art" role="img" aria-label="Gold diamond engagement ring with matching band" style="left:339px;top:134px;width:231px;height:130px;background:radial-gradient(ellipse,#f3dcc0 0,#e0a064 45%,rgba(196,96,15,0) 72%)"></div>
    <h2 class="hero-title" style="left:111px;top:52px;font-size:34px">Bright Brilliant<br>Classic</h2>
    <a class="btn" href="#" style="left:111px;top:160px">Shop Now</a>
  </div>
  <div class="hero-tile tile-grey">
    <div class="hero-photo" role="img" aria-label="Pair of interlocked polished silver wedding bands on a hand"></div>
    <h2 class="hero-title" style="left:29px;top:306px;font-size:41px">Calm Sophisticated<br>Elegant</h2>
    <a class="btn" href="#" style="left:31px;top:429px">Shop Now</a>
  </div>
</section>

<section class="categories">
  <div class="sec-title" style="top:91px"><h2>Categories</h2></div>
  <div class="cat-grid">
    <a class="cat-card" href="#" style="background:var(--cat-black)"><div class="ring-art" role="img" aria-label="Black patterned ring" style="background:radial-gradient(ellipse,#111 30%,#555 55%,#000 75%)"></div><span>Black Collection</span></a>
    <a class="cat-card" href="#" style="background:var(--cat-silver)"><div class="ring-art" role="img" aria-label="Silver ring" style="background:radial-gradient(ellipse,#54575b 30%,#d8d8d8 55%,#54575b 75%)"></div><span>Silver Collection</span></a>
    <a class="cat-card" href="#" style="background:var(--cat-blue)"><div class="ring-art" role="img" aria-label="Black and blue ring" style="background:radial-gradient(ellipse,#0b3270 30%,#1f6fe0 50%,#111 62%,#0b3270 76%)"></div><span>Blue Collection</span></a>
    <a class="cat-card" href="#" style="background:var(--cat-gold)"><div class="ring-art" role="img" aria-label="Gold ring" style="background:radial-gradient(ellipse,#e2aa2a 30%,#fff0b0 52%,#e8b830 64%,#e2aa2a 76%)"></div><span>Gold Collection</span></a>
    <a class="cat-card" href="#" style="background:var(--cat-brown)"><div class="ring-art" role="img" aria-label="Black ring with wood inlay" style="background:radial-gradient(ellipse,#83553f 30%,#1a1a1a 50%,#a0402a 58%,#83553f 76%)"></div><span>Brown Collection</span></a>
    <a class="cat-card" href="#" style="background:var(--cat-rose)"><div class="ring-art" role="img" aria-label="Grey ring with rose gold inlay" style="background:radial-gradient(ellipse,#d9985f 30%,#f0c09a 50%,#9a9a9a 60%,#d9985f 76%)"></div><span>Rose Gold Collection</span></a>
  </div>
</section>

<section class="products">
  <div class="sec-title on-dark" style="top:88px"><h2>Our Products</h2></div>
  <div class="tabs"><a class="active" href="#">Top Rated</a><a href="#">Customer Favorites</a></div>
  <div class="prod-grid">
    <div class="prod-card"><span class="stars">★★★★☆</span><div class="ring-art" role="img" aria-label="Silver and black tungsten band" style="background:radial-gradient(ellipse,#262626 32%,#e6e6e6 50%,#444 70%,rgba(38,38,38,0) 72%)"></div><p>The Vanguard – Men's Tungsten Ring – Silver Black Gold Band for Him 6mm or 8mm</p><strong>$99.00</strong></div>
    <div class="prod-card"><span class="stars">★★★★☆</span><div class="ring-art" role="img" aria-label="Polished silver tungsten band" style="background:radial-gradient(ellipse,#262626 32%,#f0f0f0 50%,#8a8a8a 70%,rgba(38,38,38,0) 72%)"></div><p>The Vanguard – Men's Tungsten Ring – Silver Black Gold Band for Him 6mm or 8mm</p><strong>$99.00</strong></div>
    <div class="prod-card"><span class="stars">★★★★☆</span><div class="ring-art" role="img" aria-label="Silver band with gear pattern inlay" style="background:radial-gradient(ellipse,#262626 32%,#cfcfcf 48%,#2a2a2a 58%,#9a9a9a 70%,rgba(38,38,38,0) 72%)"></div><p>The Vanguard – Men's Tungsten Ring – Silver Black Gold Band for Him 6mm or 8mm</p><strong>$99.00</strong></div>
    <div class="prod-card"><span class="stars">★★★★☆</span><div class="ring-art" role="img" aria-label="Brushed silver dome band" style="background:radial-gradient(ellipse,#262626 32%,#dcdcdc 50%,#7a7a7a 70%,rgba(38,38,38,0) 72%)"></div><p>The Vanguard – Men's Tungsten Ring – Silver Black Gold Band for Him 6mm or 8mm</p><strong>$99.00</strong></div>
    <div class="prod-card"><span class="stars">★★★★☆</span><div class="ring-art" role="img" aria-label="Silver band with hammered gold inlay" style="background:radial-gradient(ellipse,#262626 32%,#d9b27a 50%,#9a9a9a 70%,rgba(38,38,38,0) 72%)"></div><p>The Vanguard – Men's Tungsten Ring – Silver Black Gold Band for Him 6mm or 8mm</p><strong>$99.00</strong></div>
    <div class="prod-card"><span class="stars">★★★★☆</span><div class="ring-art" role="img" aria-label="Two-tone silver and gold band" style="background:radial-gradient(ellipse,#262626 32%,#e9e9e9 48%,#e0a820 62%,rgba(38,38,38,0) 72%)"></div><p>The Vanguard – Men's Tungsten Ring – Silver Black Gold Band for Him 6mm or 8mm</p><strong>$99.00</strong></div>
    <div class="prod-card"><span class="stars">★★★★☆</span><div class="ring-art" role="img" aria-label="Gold grooved band" style="background:radial-gradient(ellipse,#262626 32%,#fff06a 48%,#d8a800 66%,rgba(38,38,38,0) 72%)"></div><p>The Vanguard – Men's Tungsten Ring – Silver Black Gold Band for Him 6mm or 8mm</p><strong>$99.00</strong></div>
    <div class="prod-card"><span class="stars">★★★★☆</span><div class="ring-art" role="img" aria-label="Brushed gold band" style="background:radial-gradient(ellipse,#262626 32%,#f4cc50 50%,#c79a1c 68%,rgba(38,38,38,0) 72%)"></div><p>The Vanguard – Men's Tungsten Ring – Silver Black Gold Band for Him 6mm or 8mm</p><strong>$99.00</strong></div>
  </div>
  <a class="btn view-more" href="#">View More</a>
</section>

<section class="engrave">
  <h2>Engraving The Ring&nbsp; With Names, Dates, Or Special Messages.</h2>
  <p>Lorem ipsum dolor sit amet, consectetur adipiscing do eiusmod tempor incididunt ut labore et dolore magna aliqua. Quis ipsum suspendisse ultrices gravida. Risus commodo viverra maecenas accumsan</p>
  <a class="btn" href="#">Make It Yours</a>
  <div class="engrave-back"></div>
  <div class="engrave-photo" role="img" aria-label="Gold band with engraved message inside, resting on white fabric"></div>
</section>

<section class="testimonials">
  <div class="sec-title" style="top:0"><h2>Clients Testimonials</h2></div>
  <div class="testi-grid">
    <div class="testi-card"><p>Lorem ipsum dolor sit amet, con sectetur adipi scing elit, sed do ei usmod tempor incid idunt ut labore et dolore magna aliqua</p><div class="avatar" role="img" aria-label="Customer photo"></div><span class="who">Alexander</span><span class="stars">★★★★☆</span></div>
    <div class="testi-card"><p>Lorem ipsum dolor sit amet, con sectetur adipi scing elit, sed do ei usmod tempor incid idunt ut labore et dolore magna aliqua</p><div class="avatar" role="img" aria-label="Customer photo"></div><span class="who">Alexander</span><span class="stars">★★★★☆</span></div>
    <div class="testi-card"><p>Lorem ipsum dolor sit amet, con sectetur adipi scing elit, sed do ei usmod tempor incid idunt ut labore et dolore magna aliqua</p><div class="avatar" role="img" aria-label="Customer photo"></div><span class="who">Alexander</span><span class="stars">★★★★☆</span></div>
    <div class="testi-card"><p>Lorem ipsum dolor sit amet, con sectetur adipi scing elit, sed do ei usmod tempor incid idunt ut labore et dolore magna aliqua</p><div class="avatar" role="img" aria-label="Customer photo"></div><span class="who">Alexander</span><span class="stars">★★★★☆</span></div>
    <div class="testi-card"><p>Lorem ipsum dolor sit amet, con sectetur adipi scing elit, sed do ei usmod tempor incid idunt ut labore et dolore magna aliqua</p><div class="avatar" role="img" aria-label="Customer photo"></div><span class="who">Alexander</span><span class="stars">★★★★☆</span></div>
    <div class="testi-card"><p>Lorem ipsum dolor sit amet, con sectetur adipi scing elit, sed do ei usmod tempor incid idunt ut labore et dolore magna aliqua</p><div class="avatar" role="img" aria-label="Customer photo"></div><span class="who">Alexander</span><span class="stars">★★★★☆</span></div>
  </div>
</section>

<section class="benefits">
  <div class="sec-title on-dark" style="top:88px"><h2>Our Benefits</h2></div>
  <div class="benefit" style="left:113px">
    <svg width="136" height="84" viewBox="0 0 136 84" fill="none" stroke="#ffc400" stroke-width="4"><rect x="10" y="4" width="78" height="56"/><path d="M88 24h26l16 20v16H88z"/><circle cx="34" cy="68" r="9"/><circle cx="108" cy="68" r="9"/><path d="M36 30l10 10 20-20"/><path d="M2 50h20M2 60h14"/></svg>
    Free Delivery</div>
  <div class="benefit" style="left:358px">
    <svg width="90" height="84" viewBox="0 0 90 84" fill="none" stroke="#ffc400" stroke-width="4"><path d="M45 6l34 16v38L45 78 11 60V22z"/><path d="M11 22l34 16 34-16M45 38v40"/><path d="M56 58c10 0 16-6 16-14M62 52l-6 6 6 6"/></svg>
    Free Returns</div>
  <div class="benefit" style="left:602px">
    <svg width="90" height="84" viewBox="0 0 90 84" fill="none" stroke="#ffc400" stroke-width="4"><rect x="30" y="4" width="30" height="26"/><rect x="6" y="44" width="30" height="30"/><rect x="50" y="44" width="30" height="30"/><circle cx="62" cy="40" r="10"/><path d="M57 40l4 4 7-8"/></svg>
    Every Ring Stock</div>
  <div class="benefit" style="left:847px">
    <svg width="116" height="84" viewBox="0 0 116 84" fill="none" stroke="#ffc400" stroke-width="4"><path d="M70 4l36 16v40L70 80 34 60V20z"/><path d="M34 20l36 16 36-16M70 36v44"/><path d="M4 30h22M10 44h18M4 58h22"/></svg>
    Fast Delivery</div>
</section>

<footer class="footer">
  <a class="brand" href="#"><span class="brand-dot" style="width:72px;height:72px"></span><span class="brand-name" style="font-size:21px">KESTREL HOOPS</span></a>
  <p class="about">Lorem ipsum dolor sit amet, consectetur dipiscing elit, sed do eiusmod tempor incididunt</p>
  <div class="foot-col" style="left:609px">
    <h3>Quick Links</h3>
    <ul><li>Free Ring Sizer</li><li>Free Delivery</li><li>Returns And Exchanges</li><li>Try At Home</li><li>Ring Engraving</li></ul>
  </div>
  <div class="foot-col" style="left:918px">
    <h3>Important Links</h3>
    <ul><li>Contact Us</li><li>Terms of Service</li><li>Privacy Policy</li><li>Blog</li></ul>
  </div>
  <div class="foot-rule"></div>
  <p class="copyright">© 2024 Kestrel Hoops. All Rights Reserved.</p>
  <div class="pay" aria-label="Accepted payment methods"><i></i><i></i><i></i><i></i><i></i><i></i><i></i><i></i></div>
</footer>

</body>
</html>
```